wine label for ultra premium vineyard in Bendigo, Central Otago, New Zealand

"WREN" is our new wine brand, with grapes grown in our spectacular "ter Hoeven" vineyard. The small, elevated vineyard overlooks a river valley and snowy mountains. We would like a highly elegant label for our 2018 pinot noir wine, which highlights the quality of wine and our very special vineyard location. "WREN" has to be prominent, with secondary emphasis on "ter Hoeven vineyard" and "Bendigo, Central Otago". A stylized WREN logo (bird) could be a useful design device instead of the commonly seen illustrated mountain landscape (which is quite common for our local wines). Label size 90 high, 110 wide. Please use a pinot noir / burgundy bottle. See here for vineyard pics, and also below pics for other local wine labels and pics for inspiration / styles. https://www.instagram.com/jan.ter.hoeven/

Target Market(s)

average bottle price for this premium red pinot noir would be aroundUS$40. target market are generally urban professionals aged 25 and older with a high degree of interest in pinot noir wine, and who are familiar with New Zealand pinot noir (ie. already know several brands).

Colors
ed252d

Requirements
Must have
• distinctive label, sophisticated look
Nice to have
• classy white paper stock
Should not have
• label must not get too busy... less but high quality and distinctive is more....

```html
<!DOCTYPE html>
<html lang="en">
<head>
<meta charset="utf-8">
<title>WREN Pinot Noir 2018 – Label</title>
<link rel="stylesheet" href="https://fonts.googleapis.com/css2?family=Bodoni+Moda:wght@400&family=Sacramento&family=Lato:wght@400&family=Cormorant+Garamond:wght@700&family=Pinyon+Script&display=swap">
<style>
  :root {
    --page: #ffffff;
    --paper: #efefed;
    --paper-shade: #e6e6e3;
    --ink: #121212;
    --ink-soft: #2a2a2a;
    --band: #15161d;
    --band-text: #f4f4f2;
    --art-light: #d9d9d6;
    --art-dark: #8d8d8a;
  }
  * { margin: 0; padding: 0; box-sizing: border-box; }
  html, body {
    width: 1200px;
    height: 2980px;
    overflow: hidden;
    background: var(--page);
  }
  .canvas {
    position: relative;
    width: 1200px;
    height: 2980px;
    background: var(--page);
  }
  .label {
    position: absolute;
    left: 0;
    top: 999px;
    width: 1200px;
    height: 982px;
    background:
      radial-gradient(ellipse at 30% 20%, rgba(255,255,255,0.6), transparent 60%),
      linear-gradient(180deg, var(--paper) 0%, var(--paper-shade) 100%);
    overflow: hidden;
  }
  .brand {
    position: absolute;
    left: 64px;
    top: 23px;
    font-family: "Bodoni Moda", serif;
    font-weight: 400;
    font-size: 300px;
    line-height: 1;
    letter-spacing: 12px;
    color: var(--ink);
    white-space: nowrap;
    transform: scaleX(0.9);
    transform-origin: left top;
  }
  .vineyard {
    position: absolute;
    left: 72px;
    top: 391px;
    font-family: "Sacramento", cursive;
    font-size: 100px;
    line-height: 1;
    color: var(--ink);
    white-space: nowrap;
  }
  .region {
    position: absolute;
    left: 64px;
    top: 584px;
    font-family: "Lato", sans-serif;
    font-weight: 400;
    font-size: 62px;
    line-height: 1;
    color: var(--ink-soft);
    white-space: nowrap;
  }
  .vintage {
    position: absolute;
    left: 66px;
    top: 720px;
    font-family: "Cormorant Garamond", serif;
    font-weight: 700;
    font-size: 50px;
    line-height: 1;
    color: var(--ink);
  }
  .bird-art {
    position: absolute;
    left: 706px;
    top: 310px;
    width: 463px;
    height: 405px;
  }
  .variety-band {
    position: absolute;
    left: 0;
    top: 792px;
    width: 1200px;
    height: 190px;
    background: var(--band);
    display: flex;
    align-items: center;
    justify-content: center;
  }
  .variety {
    font-family: "Pinyon Script", cursive;
    font-size: 104px;
    letter-spacing: 8px;
    color: var(--band-text);
    line-height: 1;
    white-space: nowrap;
  }
</style>
</head>
<body>
<main class="canvas">
  <section class="label">
    <h1 class="brand">WREN</h1>
    <p class="vineyard">ter Hoeven vineyard</p>
    <p class="region">Bendigo, Central Otago</p>
    <p class="vintage">2018</p>
    <svg class="bird-art" viewBox="0 0 463 405" role="img" aria-label="Engraved illustration of a small bird at its nest among flowering branches">
      <defs>
        <radialGradient id="artTone" cx="50%" cy="55%" r="55%">
          <stop offset="0%" stop-color="#8d8d8a" stop-opacity="0.55"/>
          <stop offset="100%" stop-color="#d9d9d6" stop-opacity="0"/>
        </radialGradient>
      </defs>
      <rect x="0" y="0" width="463" height="405" fill="url(#artTone)"/>
    </svg>
    <div class="variety-band">
      <p class="variety">Pinot Noir</p>
    </div>
  </section>
</main>
</body>
</html>
```